Modern Business Card For A Digital Advertising Company

I'll be print on the Pell Prints Velour paper http://us.pellprints.com/products/velour/business-cards.html
Need's to be modern and use the color palette of the logo or gray scales. I think integrating the pixelation of the logo in to the card and having it wrap from one side to the other could be interesting. My company provides ad operations, web development, and number of other services to websites around the world. You can see my website at http://www.zantorhq.com
Contact info on the card needs to have
Owen Lasko
President
p.318.204.6637
owen@zantorhq.com
http://www.zantorhq.com
Doesn't necessarily need to be in that order
Website owners
Business

```html
<!DOCTYPE html>
<html lang="en">
<head>
<meta charset="utf-8">
<title>Zantor HQ Business Card</title>
<link rel="stylesheet" href="https://fonts.googleapis.com/css2?family=Arimo:wght@400;700&display=swap">
<style>
  :root {
    --stage: #2d2d2d;
    --card: #ffffff;
    --card-edge: #c9c9c9;
    --green: #8dc33f;
    --ink: #4a4a40;
    --text: #1e1e1e;
    --black: #111111;
  }
  html, body {
    margin: 0;
    width: 1200px;
    height: 518px;
    overflow: hidden;
    background: var(--stage);
    font-family: "Arimo", Arial, sans-serif;
  }
  .stage { position: relative; width: 1200px; height: 518px; }
  .card {
    position: absolute;
    top: 100px;
    width: 550px;
    height: 316px;
    background: var(--card);
    border: 2px solid var(--card-edge);
    border-radius: 22px;
    box-sizing: border-box;
    overflow: hidden;
  }
  .card--front { left: 37px; }
  .card--back { left: 617px; }
  .card__wave { position: absolute; left: 0; top: 0; width: 550px; height: 316px; }
  .brand {
    position: absolute;
    display: flex;
    align-items: center;
    gap: 10px;
    font-weight: 700;
    color: var(--green);
    letter-spacing: 1px;
    white-space: nowrap;
  }
  .brand__mark { width: 22px; height: 22px; background: var(--green); }
  .card--front .brand { left: 62px; top: 166px; font-size: 26px; }
  .card--back .brand { left: 0; width: 550px; justify-content: center; top: 124px; font-size: 34px; }
  .card--back .brand__mark { width: 28px; height: 28px; }
  .holder { position: absolute; right: 32px; top: 30px; text-align: right; }
  .holder__name { font-size: 19px; font-weight: 700; color: var(--ink); margin: 0; line-height: 22px; }
  .holder__title { font-size: 15px; color: var(--text); margin: 0; line-height: 20px; }
  .divider { position: absolute; left: 307px; top: 108px; width: 1px; height: 101px; background: var(--text); }
  .contact { position: absolute; left: 323px; top: 128px; margin: 0; padding: 0; list-style: none; }
  .contact__item { display: flex; align-items: center; gap: 8px; height: 25px; font-size: 15px; color: var(--text); }
  .contact__icon { width: 15px; height: 15px; }
</style>
</head>
<body>
<div class="stage">
  <section class="card card--front">
    <div class="brand"><span class="brand__mark"></span>ZANTOR HQ</div>
    <div class="holder">
      <p class="holder__name">Owen Lasko</p>
      <p class="holder__title">President</p>
    </div>
    <div class="divider"></div>
    <ul class="contact">
      <li class="contact__item">
        <svg class="contact__icon" viewBox="0 0 16 16"><circle cx="8" cy="8" r="7" fill="none" stroke="#3a9a3a" stroke-width="1.2"/><path d="M5.5 4.5l1.5 0 .6 2-1 .8c.5 1 1.1 1.6 2 2l.8-1 2 .6v1.5c-3.5.3-6.2-2.4-5.9-5.9z" fill="#3a9a3a"/></svg>
        318-204-6637
      </li>
      <li class="contact__item">
        <svg class="contact__icon" viewBox="0 0 16 16"><rect x="1.5" y="3.5" width="13" height="9" fill="none" stroke="#3a9a3a" stroke-width="1.2"/><path d="M1.5 3.5l6.5 5 6.5-5" fill="none" stroke="#3a9a3a" stroke-width="1.2"/></svg>
        owen@zantorhq.com
      </li>
      <li class="contact__item">
        <svg class="contact__icon" viewBox="0 0 16 16"><circle cx="8" cy="8" r="7" fill="#3a9a3a"/><path d="M1 8h14M8 1c-3 3.5-3 10.5 0 14M8 1c3 3.5 3 10.5 0 14M2.5 4.5h11M2.5 11.5h11" stroke="#fff" stroke-width="0.9" fill="none"/></svg>
        www.zantorhq.com
      </li>
    </ul>
    <svg class="card__wave" viewBox="0 0 550 316" aria-hidden="true">
      <path d="M0 266 C120 292 220 219 330 219 C430 219 490 258 550 266 L550 316 L0 316 Z" fill="var(--black)"/>
      <path d="M0 282 C120 306 220 232 330 232 C430 232 490 272 550 282 L550 316 L0 316 Z" fill="var(--green)"/>
    </svg>
  </section>

  <section class="card card--back">
    <div class="brand"><span class="brand__mark"></span>ZANTOR HQ</div>
    <svg class="card__wave" viewBox="0 0 550 316" aria-hidden="true">
      <path d="M0 274 C90 230 150 218 230 220 C350 224 450 262 550 266 L550 316 L0 316 Z" fill="var(--black)"/>
      <path d="M0 290 C90 244 150 232 230 234 C350 238 450 276 550 280 L550 316 L0 316 Z" fill="var(--green)"/>
    </svg>
  </section>
</div>
</body>
</html>
```